Redesign Of Current Landing Page

I need to redesign this landing page https://www.brightlanepromo.biz/?page=landing&landing=23 (Please do not opt in because when you do it will show you the home page. Please clear your cookies before going to this url above to view the 1 page landing page.)

Please use my updated website as a reference for colors and logo.
http://sitecradlewerk.com/dh/bpq/index.html

I would like the call to action to be a button that opens into a lead form...

Button would be "Download Samples"

Target Market(s)

small business owners

Industry/Entity Type

Marketing

Number of Pages Required

1 page

Colors

Designer to choose colors to be used in the design.

Requirements
Must have
• must be full responsive on all devices
Nice to have
• must have a legitimate professional apeal to it
Should not have
• open

```html
<!DOCTYPE html>
<html lang="en">
<head>
<meta charset="utf-8">
<title>BLPG — Attract More Customers</title>
<link href="https://fonts.googleapis.com/css2?family=Anton&family=Montserrat:wght@400;500;600;700&family=Open+Sans:ital,wght@0,400;0,600;0,700;1,400&display=swap" rel="stylesheet">
<style>
:root{
  --blue:#0a6fc2;
  --blue-dark:#0b5aa0;
  --orange:#f9a400;
  --ink:#2b2b2b;
  --muted:#6b6b6b;
  --light:#f6f6f6;
  --white:#ffffff;
}
*{margin:0;padding:0;box-sizing:border-box}
html,body{width:1200px;height:2219px;overflow:hidden}
body{position:relative;font-family:"Open Sans",Arial,sans-serif;color:var(--ink);background:var(--white)}
.abs{position:absolute}

/* header */
.site-header{position:absolute;left:0;top:0;width:1200px;height:100px;background:var(--white);border-bottom:4px solid var(--blue)}
.brand{position:absolute;left:132px;top:32px;display:flex;align-items:center;gap:10px}
.brand-dot{width:40px;height:40px;border-radius:50%;background:var(--blue)}
.brand-name{font-family:"Montserrat",sans-serif;font-weight:700;font-size:30px;color:var(--ink);letter-spacing:1px}
.contact-row{position:absolute;right:132px;top:19px;display:flex;gap:22px;font-size:12px;color:var(--muted);align-items:center}
.contact-row b{color:var(--blue);font-size:15px;font-weight:600}
.contact-row svg{vertical-align:-2px;margin-right:6px}
.main-nav{position:absolute;top:60px;left:0;font-family:"Montserrat",sans-serif;font-weight:600;font-size:12px;color:var(--ink)}
.main-nav span{position:absolute;white-space:nowrap}
.main-nav .active{color:var(--blue)}
.search-btn{position:absolute;left:1033px;top:50px;width:35px;height:35px;border-radius:50%;background:#e2e2e2;display:flex;align-items:center;justify-content:center}

/* hero */
.hero{position:absolute;left:0;top:100px;width:1200px;height:493px;
  background:radial-gradient(ellipse at 72% 55%,#f1a33b 0%,#b8693a 18%,rgba(60,55,60,0) 45%),
  linear-gradient(180deg,#5d6774 0%,#4b505a 40%,#2b2a2d 70%,#1b1c22 100%)}
.hero-kicker{position:absolute;left:132px;top:94px;font-family:"Anton",Impact,sans-serif;font-size:40px;line-height:1;color:var(--white);letter-spacing:1.5px}
.hero-title{position:absolute;left:130px;top:148px;font-family:"Anton",Impact,sans-serif;font-size:80px;line-height:1;color:var(--white);letter-spacing:3px}
.hero-sub{position:absolute;left:132px;top:238px;font-weight:700;font-size:17px;line-height:30px;color:var(--white)}
.btn{position:absolute;display:flex;align-items:center;justify-content:center;text-align:center;white-space:nowrap;border-radius:22px;font-family:"Open Sans",Arial,sans-serif;font-weight:600;font-size:11.5px;color:var(--white);text-transform:uppercase}
.btn-orange{background:var(--orange)}
.btn-blue{background:var(--blue)}
.dot{position:absolute;top:426px;width:15px;height:15px;border-radius:50%;border:2px solid var(--white)}
.dot.on{background:var(--orange);border-color:var(--orange)}

/* imagine */
.imagine{position:absolute;left:0;top:593px;width:1200px;height:375px;background:linear-gradient(180deg,#e9ebee 0%,#f3f4f6 55%,#e6e8ec 100%)}
.section-title{position:absolute;left:0;width:1200px;text-align:center;font-family:"Montserrat",sans-serif;font-weight:500;color:var(--ink)}
.imagine p{position:absolute;left:220px;width:760px;text-align:center;font-size:11px;line-height:21px;color:#444}

/* how */
.how{position:absolute;left:0;top:968px;width:1200px;height:327px}
.how-title{position:absolute;left:629px;top:46px;font-family:"Montserrat",sans-serif;font-weight:600;font-size:26px;color:var(--white)}
.how p{position:absolute;left:629px;width:450px;font-size:10.8px;line-height:20px;color:var(--white)}

/* why */
.why{position:absolute;left:0;top:1295px;width:1200px;height:488px;background:var(--light)}
.feature{position:absolute;width:300px}
.feature-icon{position:absolute;left:0;top:0;width:53px;height:53px;border-radius:50%;border:1.5px solid var(--blue);display:flex;align-items:center;justify-content:center;background:var(--white)}
.feature h3{position:absolute;left:68px;top:4px;width:215px;font-family:"Montserrat",sans-serif;font-weight:400;font-size:14.5px;line-height:21px;color:#333}
.feature p{position:absolute;left:68px;top:48px;width:215px;font-size:11px;line-height:19px;color:var(--muted)}

/* testimonial */
.testimonial{position:absolute;left:0;top:1783px;width:1200px;height:326px;background:var(--white)}
.avatar{position:absolute;left:547px;top:42px;width:106px;height:106px;border-radius:50%;border:4px solid #d9d9d9;background:linear-gradient(180deg,#e9e3de,#c9b5a4)}
.quote-text{position:absolute;left:185px;top:162px;width:840px;text-align:center;font-style:italic;font-size:11px;line-height:22.5px;color:#444}
.quote-mark{position:absolute;font-family:Georgia,serif;font-size:38px;line-height:1;color:#777;font-style:italic}
.quote-close{font-family:Georgia,serif;font-size:30px;line-height:0;color:#777;position:relative;top:14px;margin-left:14px}
.person{position:absolute;left:0;width:1200px;text-align:center;font-family:"Montserrat",sans-serif;font-weight:700}

/* footer */
.site-footer{position:absolute;left:0;top:2109px;width:1200px;height:110px;background:var(--light);border-top:4px solid var(--blue)}
.footer-links{position:absolute;left:294px;top:36px;font-size:11px;color:#444}
.copyright{position:absolute;left:294px;top:61px;font-size:11px;color:#444}
.social{position:absolute;top:44px;width:29px;height:29px;border-radius:50%}
</style>
</head>
<body>

<header class="site-header">
  <div class="brand"><span class="brand-dot"></span><span class="brand-name">BLPG</span></div>
  <div class="contact-row">
    <span><svg width="11" height="11" viewBox="0 0 24 24"><path fill="#0a6fc2" d="M6.6 10.8a15 15 0 0 0 6.6 6.6l2.2-2.2a1 1 0 0 1 1-.25 11.4 11.4 0 0 0 3.6.57 1 1 0 0 1 1 1V20a1 1 0 0 1-1 1A17 17 0 0 1 3 4a1 1 0 0 1 1-1h3.5a1 1 0 0 1 1 1c0 1.25.2 2.45.57 3.57a1 1 0 0 1-.25 1z"/></svg>Phone Number : <b>1-800-555-0147</b></span>
    <span><svg width="11" height="11" viewBox="0 0 24 24"><circle cx="12" cy="12" r="10" fill="none" stroke="#0a6fc2" stroke-width="3"/><path d="M12 7v5l3 2" stroke="#0a6fc2" stroke-width="2.5" fill="none"/></svg>Time : <b>Mon-Fri 8am-5pm PST</b></span>
  </div>
  <nav class="main-nav">
    <span class="active" style="left:438px">HOME</span>
    <span style="left:520px">ABOUT US</span>
    <span style="left:623px">SERVICES</span>
    <span style="left:722px">TESTIMONIALS</span>
    <span style="left:851px">BLOG</span>
    <span style="left:929px">CONTACT US</span>
  </nav>
  <div class="search-btn"><svg width="12" height="12" viewBox="0 0 24 24"><circle cx="10" cy="10" r="6.5" fill="none" stroke="#555" stroke-width="3"/><path d="M15 15l6 6" stroke="#555" stroke-width="3"/></svg></div>
</header>

<section class="hero" role="img" aria-label="Photo of a seaside resort terrace with a thatched pavilion at sunset">
  <div class="hero-kicker">ATTRACT MORE</div>
  <div class="hero-title">CUSTOMERS</div>
  <div class="hero-sub">Who Spend More Money With Your Business More Often<br>Using Free Vacation &amp; Cruise Certificates And Other Incentives<br>Without Breaking The Bank!</div>
  <div class="btn btn-orange" style="left:132px;top:357px;width:310px;height:39px">Download Free Samples Of Our Incentives</div>
  <span class="dot on" style="left:561px"></span>
  <span class="dot" style="left:593px"></span>
  <span class="dot" style="left:625px"></span>
</section>

<section class="imagine" role="img" aria-label="Faded photo of a resort building at dusk">
  <h2 class="section-title" style="top:70px;font-size:26px">IMAGINE</h2>
  <p style="top:115px">being able to create exciting give away promotions that will boost your sales without ever having to worry about cost.Brightlane Promo Group, Inc. provides high-perceived value promotional incentives to businesses that want to advertise an exciting Give Away that will instantly attract more customers from your existing advertising efforts.</p>
  <p style="top:191px">Your business can give away incentive certificates that are redeemable for luxury hotel &amp; resort stays with airfare included, cruises, cash for gas, groceries, dining and even electronic goods.</p>
  <div class="btn btn-orange" style="left:444px;top:258px;width:312px;height:40px">Download Free Samples Of Our Incentives</div>
</section>

<section class="how">
  <svg class="abs" style="left:0;top:0" width="1200" height="327" viewBox="0 0 1200 327">
    <defs>
      <linearGradient id="poolGrad" x1="0" y1="0" x2="0" y2="1">
        <stop offset="0" stop-color="#6f7fa6"/>
        <stop offset="0.45" stop-color="#e0a070"/>
        <stop offset="0.6" stop-color="#3b5a86"/>
        <stop offset="1" stop-color="#0f2440"/>
      </linearGradient>
    </defs>
    <rect width="1200" height="327" fill="#f9a400"/>
    <path d="M0 0 H550 Q635 163 548 327 H0 Z" fill="url(#poolGrad)" role="img" aria-label="Photo of loungers and umbrellas beside an infinity pool at sunset"/>
    <path d="M550 0 Q635 163 548 327" fill="none" stroke="#fff" stroke-width="4"/>
  </svg>
  <h2 class="how-title">HOW CAN WE DO IT?</h2>
  <p style="top:88px">We help fill empty rooms for thousands of hotels and resorts in hundreds of destinations around the world as well as the major cruise lines. Hotels and resorts are rarely full so when we place someone in their empty rooms, they end up making...</p>
  <p style="top:163px">We also help over 18,000 restaurants, electronic manufacturers, the major gas companies and top grocery chains in the U.S and Canada increase brand...</p>
  <div class="btn btn-blue" style="left:629px;top:228px;width:309px;height:40px">Download Free Samples Of Our Incentives</div>
</section>

<section class="why">
  <h2 class="section-title" style="top:55px;font-size:27px">WHY OFFER INCENTIVES TO CUSTOMERS?</h2>

  <div class="feature" style="left:132px;top:129px">
    <div class="feature-icon"><svg width="24" height="20" viewBox="0 0 24 20"><path d="M1 1v18h22" stroke="#0a6fc2" stroke-width="2" fill="none"/><rect x="5" y="9" width="3" height="8" fill="#0a6fc2"/><rect x="10" y="5" width="3" height="12" fill="#0a6fc2"/><rect x="15" y="11" width="3" height="6" fill="#0a6fc2"/><rect x="20" y="7" width="2" height="10" fill="#0a6fc2"/></svg></div>
    <h3>Increase Responses From Your Existing Ads</h3>
    <p>Phasellus facilisis, nunc in undo tump lacin auctor, eros lacus...</p>
  </div>
  <div class="feature" style="left:462px;top:129px">
    <div class="feature-icon"><svg width="22" height="22" viewBox="0 0 24 24"><path d="M21 6.5a5 5 0 0 1-6.8 4.7L5 20.4a1.9 1.9 0 0 1-2.7-2.7l9.2-9.2A5 5 0 0 1 17.5 2l-3 3 .7 3.8 3.8.7z" fill="#0a6fc2"/></svg></div>
    <h3>#1 Sales Closing Tool - Gift w/ Purchase</h3>
    <p>Phasellus facilisis, nunc in undo tump lacin auctor, eros lacus...</p>
  </div>
  <div class="feature" style="left:796px;top:129px">
    <div class="feature-icon"><svg width="22" height="22" viewBox="0 0 24 24"><path d="M12 2l2.9 6.3 6.9.7-5.2 4.6 1.5 6.8L12 16.9 5.9 20.4l1.5-6.8L2.2 9l6.9-.7z" fill="none" stroke="#0a6fc2" stroke-width="2" stroke-linejoin="round"/></svg></div>
    <h3>Build Brand Awareness and Trust</h3>
    <p>Phasellus facilisis, nunc in undo tump lacin auctor, eros lacus...</p>
  </div>

  <div class="feature" style="left:132px;top:265px">
    <div class="feature-icon"><svg width="24" height="24" viewBox="0 0 24 24"><path d="M2 12a10 10 0 0 1 20 0z" fill="#0a6fc2"/><path d="M12 12v7a2 2 0 0 1-4 0" stroke="#0a6fc2" stroke-width="2" fill="none"/></svg></div>
    <h3>Insure The Sale Over Your Competition</h3>
    <p>Phasellus facilisis, nunc in undo tump lacin auctor, eros lacus...</p>
  </div>
  <div class="feature" style="left:462px;top:265px">
    <div class="feature-icon"><svg width="24" height="22" viewBox="0 0 24 22"><rect x="1" y="6" width="22" height="15" rx="2" fill="#0a6fc2"/><path d="M8 6V3h8v3" stroke="#0a6fc2" stroke-width="2" fill="none"/><rect x="1" y="12" width="22" height="1.5" fill="#fff"/></svg></div>
    <h3>Boost Repeat and Referral Business-</h3>
    <p>Phasellus facilisis, nunc in undo tump lacin auctor, eros lacus...</p>
  </div>
  <div class="feature" style="left:796px;top:265px">
    <div class="feature-icon"><span style="font-family:'Montserrat',sans-serif;font-weight:600;font-size:26px;color:#0a6fc2">$</span></div>
    <h3>Improve Retention<br>Rates</h3>
    <p>Phasellus facilisis, nunc in undo tump lacin auctor, eros lacus...</p>
  </div>

  <div class="btn btn-blue" style="left:444px;top:383px;width:312px;height:40px">Download Free Samples Of Our Incentives</div>
</section>

<section class="testimonial">
  <div class="avatar" role="img" aria-label="Portrait photo of the customer quoted"></div>
  <span class="quote-mark" style="left:158px;top:158px">“</span>
  <p class="quote-text">I began using your incentives two years ago to boost lead generation efforts. I have experienced a 63% increase in lead captures. And, even more importantly, my sales have increased as well. The ability to offer unlimited certificates and not having to pay for each certificate I give away is perhaps the best feature of the program, but having the flexibility to email or print certificates for my customers is also wonderful. I even use your html banners to automate my promotions right on my website.<span class="quote-close">”</span></p>
  <div class="person" style="top:242px;font-size:13px;color:var(--blue)">DAN R.</div>
  <div class="person" style="top:262px;font-size:11px;color:#555">FAIRVIEW, TN</div>
</section>

<footer class="site-footer">
  <div class="brand" style="top:34px"><span class="brand-dot"></span><span class="brand-name">BLPG</span></div>
  <div class="footer-links">HOME | ABOUT US | SERVICES | TESTIMONIALS | BLOG | CONTACT US</div>
  <div class="copyright">COPYRIGHTS © BLPG . 2017 | ALL RIGHTS RESERVED.</div>
  <span class="social" style="left:944px;background:#2d4a8c"></span>
  <span class="social" style="left:976px;background:#2aa3e6"></span>
  <span class="social" style="left:1008px;background:#e02a20"></span>
  <span class="social" style="left:1040px;background:#a6895a"></span>
</footer>

</body>
</html>
```